Wordpress Design Project for Employee Communications Site

We need a Wordpress design for a company that strategizes on and produces materials for employee communications. Improving employee communications at all levels of an organization can help improve overall company performance and results. The site needs to look very clean and professional; we're not afraid of white space. We like the functionality that Wordpress provides; however, we only want one "true" blog page; the other pages should give the impression of a more "static" web site - particularly the home page. I have a logo that I can provide.

I have added these comments to the discussion page:
Great question - thank you for asking it. I’ve done more research

I like the very clean and monochromatic looks to many of these. I don’t have to have monochromatic, but I do like minimal colors. Simple, clean, organized. The home page should “fit” almost entirely without scrolling. I do like fat footers that you can scroll down to. I don’t want a colored background, but any that I’ve chosen with colored backgrounds could be switched to a white background.

http://www.mirabelquennet.example/
http://pondraft.example/
http://v1.samplumworth.example/
http://howdythegoat.example/
http://stayingbrisk.example/
http://www.interiors.kelmun.example/
http://trelvmasters.example/

These last two are more corporate sites. The first one is from a well-respected consultant in my area who does a lot of what I do. And I think Harwenby does a nice job with their site. So, I want to marry the look I like with getting the content job done.

http://www.messagefuelbox.example/
http://www.harwenby.example/view/en_US/us/index.htm

Target Market(s)

Target market is mid- to large-sized companies. More than 500 employees.

Industry/Entity Type

Communications

Requirements
Must have
• Need an impactful home page. There should be a "blog" page; contact us; services; about. For starters, at least. I want fonts to be very readable - that is, either quite dark gray or black.
Nice to have
• I am loathe to include a picture of myself, but I do want some images that say, "professional" and "expert" in communications.
Should not have
• I don't want a hits counter :) (I know no one would do that!).

```html
<!DOCTYPE html>
<html lang="en">
<head>
<meta charset="utf-8">
<title>TSC – Teamwide Signals Company</title>
<link rel="stylesheet" href="https://fonts.googleapis.com/css2?family=Cinzel:wght@400&family=Crimson+Text:ital@1&family=Open+Sans:wght@400;600;700&family=PT+Sans+Narrow:wght@400;700&family=PT+Sans:wght@400;700&display=swap">
<style>
  :root {
    --lime: #bfd73a;
    --sky: #5bbde8;
    --ink: #2b2b2b;
    --text: #3a3a3a;
    --muted: #9a9a9a;
    --rule: #d8d8d8;
    --icon-grey: #c4c4c4;
    --photo-light: #f2f4f5;
    --photo-mid: #d9c2ae;
    --photo-dark: #9c6e50;
  }
  * { box-sizing: border-box; margin: 0; padding: 0; }
  html, body { width: 1200px; height: 1100px; overflow: hidden; background: #fff; }
  body { position: relative; font-family: "PT Sans", Arial, sans-serif; color: var(--text); }

  .top-band { position: absolute; left: 0; top: 0; width: 1200px; height: 11px; background: var(--lime); }

  .brand { position: absolute; left: 217px; top: 62px; display: flex; align-items: center; gap: 12px; }
  .brand-dot { width: 40px; height: 40px; border-radius: 50%; background: var(--lime); }
  .brand-name { font-family: "Open Sans", sans-serif; font-weight: 600; font-size: 30px; color: var(--lime); letter-spacing: 0.5px; }

  .main-nav { position: absolute; top: 176px; left: 0; width: 1200px; height: 32px; font-family: "Open Sans", sans-serif; font-weight: 700; font-size: 14.5px; color: var(--muted); }
  .main-nav a { position: absolute; top: 0; color: inherit; text-decoration: none; letter-spacing: 0.2px; }
  .main-nav a.is-current { color: var(--sky); }
  .main-nav a.is-current::after { content: ""; position: absolute; left: -7px; right: -7px; top: 27px; height: 3px; background: var(--sky); }

  .hero-shadow { position: absolute; left: 100px; top: 560px; width: 1020px; height: 70px; background: radial-gradient(ellipse 50% 40% at 50% 50%, rgba(0,0,0,0.28), rgba(0,0,0,0) 100%); }
  .hero { position: absolute; left: 210px; top: 207px; width: 800px; height: 392px; background: #fff; overflow: hidden; }
  .hero-photo { position: absolute; inset: 0; background: linear-gradient(90deg, var(--photo-dark) 0%, var(--photo-mid) 22%, #e8ddd3 40%, var(--photo-light) 55%, #fafbfb 100%); }
  .hero-title { position: absolute; left: 397px; top: 78px; font-family: "Cinzel", serif; font-weight: 400; color: #111; line-height: 1; }
  .hero-title .line-1 { display: block; font-size: 43px; letter-spacing: 0.5px; }
  .hero-title .line-2 { display: block; font-size: 37px; margin-top: 9px; letter-spacing: 0; }
  .hero-lede { position: absolute; left: 402px; top: 182px; width: 350px; font-family: "Crimson Text", serif; font-style: italic; font-size: 25px; line-height: 31px; color: #444; }

  .slider-arrow { position: absolute; top: 364px; width: 38px; height: 42px; }
  .slider-arrow.prev { left: 129px; }
  .slider-arrow.next { left: 1039px; }
  .slider-dots { position: absolute; top: 610px; left: 580px; display: flex; gap: 5px; }
  .slider-dots span { width: 14px; height: 12px; border-radius: 50%; background: #8a8a8a; }
  .slider-dots span.is-active { background: var(--sky); }

  .col-rule { position: absolute; top: 660px; width: 1px; height: 343px; background: var(--rule); }
  .row-rule { position: absolute; top: 825px; left: 205px; width: 790px; height: 1px; background: var(--rule); }

  .feature { position: absolute; width: 228px; }
  .feature-head { display: flex; align-items: center; gap: 8px; height: 36px; }
  .feature-icon { width: 32px; height: 32px; border-radius: 4px; flex: none; }
  .feature-title { font-family: "PT Sans Narrow", sans-serif; font-weight: 400; font-size: 22px; color: #222; letter-spacing: -0.2px; white-space: nowrap; }
  .feature-title.is-long { font-size: 20px; }
  .feature-body { margin-top: 5px; font-size: 12.3px; line-height: 15.6px; letter-spacing: 0.5px; text-align: justify; color: var(--text); }
  .read-more { display: flex; align-items: center; gap: 5px; margin-top: 6px; font-weight: 700; font-size: 12px; color: #222; text-decoration: none; }
  .read-more::before { content: ""; width: 14px; height: 14px; border-radius: 50%; background: var(--sky); }
  .feature-credit { margin-top: 3px; text-align: right; font-weight: 700; font-size: 12px; line-height: 14.5px; color: #333; letter-spacing: 0.3px; }

  .footer-rule { position: absolute; left: 85px; top: 1036px; width: 1030px; height: 14px; background: radial-gradient(ellipse 50% 50% at 50% 0%, rgba(0,0,0,0.22), rgba(0,0,0,0) 100%); }
  .footer-brand { position: absolute; left: 201px; top: 1056px; display: flex; align-items: center; gap: 6px; }
  .footer-brand .brand-dot { width: 20px; height: 20px; background: #a8a8a8; }
  .footer-brand .brand-name { font-size: 18px; color: #a8a8a8; }
  .footer-nav { position: absolute; top: 1051px; left: 0; width: 1200px; text-align: center; font-family: Arial, sans-serif; font-size: 13px; color: #444; }
  .footer-nav a { color: inherit; text-decoration: none; }
  .footer-nav .sep { margin: 0 15px; }
  .copyright { position: absolute; top: 1081px; left: 0; width: 1212px; text-align: center; font-family: Arial, sans-serif; font-size: 11px; color: #333; }
  .social { position: absolute; left: 906px; top: 1054px; display: flex; gap: 12px; }
  .social a { display: block; width: 26px; height: 26px; border-radius: 4px; background: var(--icon-grey); }
</style>
</head>
<body>
  <div class="top-band"></div>

  <header class="brand">
    <span class="brand-dot"></span>
    <span class="brand-name">Teamwide Signals Company</span>
  </header>

  <nav class="main-nav">
    <a class="is-current" href="#" style="left:474px">HOME</a>
    <a href="#" style="left:574px">ABOUT</a>
    <a href="#" style="left:687px">SERVICES</a>
    <a href="#" style="left:820px">BLOG</a>
    <a href="#" style="left:917px">CONTACT US</a>
  </nav>

  <div class="hero-shadow"></div>
  <section class="hero">
    <div class="hero-photo" role="img" aria-label="Photograph of a thoughtful professional man resting his head on his hand, against a bright white office background"></div>
    <h1 class="hero-title"><span class="line-1">EFFECTIVE</span><span class="line-2">COMMUNICATION</span></h1>
    <p class="hero-lede">Effective communication in the work-place is the backbone of any business.</p>
  </section>

  <svg class="slider-arrow prev" viewBox="0 0 38 42" aria-label="Previous slide"><polygon points="20,0 38,0 18,21 38,42 20,42 0,21" fill="var(--lime)"/></svg>
  <svg class="slider-arrow next" viewBox="0 0 38 42" aria-label="Next slide"><polygon points="18,0 0,0 20,21 0,42 18,42 38,21" fill="var(--lime)"/></svg>
  <div class="slider-dots"><span class="is-active"></span><span></span><span></span><span></span></div>

  <div class="col-rule" style="left:460px"></div>
  <div class="col-rule" style="left:737px"></div>
  <div class="row-rule"></div>

  <article class="feature" style="left:209px;top:645px">
    <div class="feature-head"><span class="feature-icon" role="img" aria-label="Icon of two figures in green and blue" style="background:#7fc6a0"></span><h2 class="feature-title">External Communication</h2></div>
    <p class="feature-body">Effective communication in the work-place is the backbone of any business. Without it, you could miss out on important opportunities, waste time and cause your employees and custom&shy;ers to become frustrated.</p>
    <a class="read-more" href="#">Read More</a>
  </article>
  <article class="feature" style="left:488px;top:645px">
    <div class="feature-head"><span class="feature-icon" role="img" aria-label="Icon of a red percent sign" style="background:#e2533a"></span><h2 class="feature-title">Business Growth</h2></div>
    <p class="feature-body">Effective communication in the work-place is the backbone of any business. Without it, you could miss out on important opportunities, waste time and cause your employees and custom&shy;ers to become frustrated.</p>
    <a class="read-more" href="#">Read More</a>
  </article>
  <article class="feature" style="left:764px;top:645px">
    <div class="feature-head"><span class="feature-icon" role="img" aria-label="Icon of a blue globe" style="background:#3f8fcf;border-radius:50%"></span><h2 class="feature-title">Internal Communication</h2></div>
    <p class="feature-body">Effective communication in the work-place is the backbone of any business. Without it, you could miss out on important opportunities, waste time and cause your employees and custom&shy;ers to become frustrated.</p>
    <a class="read-more" href="#">Read More</a>
  </article>

  <article class="feature" style="left:209px;top:844px">
    <div class="feature-head"><span class="feature-icon" role="img" aria-label="Icon of green and blue chat windows" style="background:#69b36a"></span><h2 class="feature-title is-long">What Customers are Saying...</h2></div>
    <p class="feature-body">TSC is a great benchmarking tool."The TSC channels offer a very effective way to communicate with geographi&shy;cally distributed stores and in a retail environment."</p>
    <p class="feature-credit" style="width:222px">Marla Denvick<br>Internal Communications<br>Manager</p>
  </article>
  <article class="feature" style="left:488px;top:844px">
    <div class="feature-head"><span class="feature-icon" role="img" aria-label="Icon of a profile head surrounded by small coloured network dots" style="background:#5a7f9c"></span><h2 class="feature-title">Internal Social Media</h2></div>
    <p class="feature-body">TSC is a great benchmarking tool."The TSC channels offer a very effective way to communicate with geographi&shy;cally distributed stores and in a retail environment."</p>
    <p class="feature-credit">Specifically for employee<br>communication</p>
  </article>
  <article class="feature" style="left:765px;top:844px">
    <div class="feature-head"><span class="feature-icon" role="img" aria-label="Icon of a rising orange bar chart" style="background:#ef8a2e"></span><h2 class="feature-title">Business Growth</h2></div>
    <p class="feature-body">TSC is a great benchmarking tool."The TSC channels offer a very effective way to communicate with geographi&shy;cally distributed stores and in a retail environment."</p>
    <p class="feature-credit" style="width:225px">Specifically for employee<br>communication</p>
  </article>

  <div class="footer-rule"></div>
  <footer>
    <div class="footer-brand"><span class="brand-dot"></span><span class="brand-name">TSC</span></div>
    <nav class="footer-nav">
      <a href="#">Home</a><span class="sep">|</span><a href="#">About</a><span class="sep">|</span><a href="#">Services</a><span class="sep">|</span><a href="#">Blog</a><span class="sep">|</span><a href="#">Contact Us</a>
    </nav>
    <p class="copyright">All rights reserved. © Teamwide Signals Company 2008</p>
    <div class="social" aria-label="Social network links"><a href="#" aria-label="Social profile"></a><a href="#" aria-label="Social profile"></a></div>
  </footer>
</body>
</html>
```